Brindle Water - 500ml

to create a water bottle packaging similar to L'onde Claire design. Bottle should be blue similar to PURE FLOW but change the design/logo to Brindle. Wording should be similar just different design and logo. Thanks.

Colors
0054AA
0677BA
7BADD7
CADEEF
E8F1F8

Requirements
Must have
• Bottle must not be in plastic bottles. They are made in a carton instead - see PURE FLOW for reference.

```html
<!DOCTYPE html>
<html lang="en">
<head>
<meta charset="utf-8">
<title>Brindle Water 500ml carton</title>
<link rel="stylesheet" href="https://fonts.googleapis.com/css2?family=Montserrat:wght@500;600;700;800&family=Kalam:wght@700&display=swap">
<style>
  :root {
    --navy: #0054AA;
    --ocean: #0677BA;
    --sky: #7BADD7;
    --mist: #CADEEF;
    --frost: #E8F1F8;
    --white: #FFFFFF;
    --stage: #EEF2F6;
  }
  * { margin: 0; padding: 0; box-sizing: border-box; }
  html, body { width: 676px; height: 1200px; overflow: hidden; background: var(--stage); }
  .canvas { position: relative; width: 676px; height: 1200px; }

  .cap {
    position: absolute; left: 298px; top: 96px; width: 80px; height: 50px;
    background: var(--white); border-radius: 8px 8px 3px 3px;
    box-shadow: inset 0 -8px 0 var(--frost);
  }
  .gable { position: absolute; left: 138px; top: 140px; width: 400px; height: 70px; }

  .carton-front {
    position: absolute; left: 138px; top: 200px; width: 400px; height: 960px;
    background: linear-gradient(180deg, var(--sky) 0%, #8DBBE0 60%, var(--mist) 80%, var(--frost) 100%);
    font-family: 'Montserrat', sans-serif; color: var(--white); text-align: center;
    overflow: hidden;
  }
  .tagline {
    position: absolute; top: 30px; width: 100%;
    font-size: 20px; font-weight: 500; letter-spacing: 1px; color: var(--frost);
  }
  .brand-band { position: absolute; left: 0; top: 68px; width: 400px; height: 240px; }
  .brand-name {
    position: absolute; top: 130px; width: 100%;
    font-size: 76px; font-weight: 800; color: var(--white); letter-spacing: 1px;
  }
  .product-type {
    position: absolute; top: 336px; width: 100%;
    font-size: 22px; font-weight: 600; color: var(--navy);
  }
  .drop-icon { position: absolute; left: 186px; top: 398px; width: 28px; height: 38px; }
  .eco-figure {
    position: absolute; top: 450px; width: 100%;
    font-size: 30px; font-weight: 700;
  }
  .eco-label {
    position: absolute; top: 490px; width: 100%;
    font-size: 20px; font-weight: 500; letter-spacing: 0.5px;
  }
  .source-line {
    position: absolute; top: 548px; width: 100%;
    font-family: 'Kalam', cursive; font-size: 40px; line-height: 52px; color: var(--white);
  }
  .mountain-art {
    position: absolute; left: 0; top: 670px; width: 400px; height: 140px;
    background: linear-gradient(180deg, var(--mist) 0%, var(--sky) 50%, var(--ocean) 80%, var(--frost) 100%);
  }
  .volume {
    position: absolute; top: 848px; width: 100%;
    font-size: 30px; font-weight: 600; color: var(--navy);
  }
  .fine-print {
    position: absolute; top: 890px; width: 100%;
    font-size: 12px; font-weight: 600; line-height: 16px; color: var(--navy);
  }
</style>
</head>
<body>
<div class="canvas">
  <div class="cap"></div>
  <svg class="gable" viewBox="0 0 400 70" aria-hidden="true">
    <polygon points="0,70 20,6 380,6 400,70" fill="#8DBBE0"/>
    <polygon points="20,6 380,6 372,0 28,0" fill="#CADEEF"/>
  </svg>

  <section class="carton-front">
    <p class="tagline">PURE &amp; REFRESHING</p>

    <svg class="brand-band" viewBox="0 0 400 240" aria-hidden="true">
      <path d="M0 0 H400 V206 C300 230 120 190 0 212 Z" fill="#0054AA"/>
      <path d="M0 212 C120 190 300 230 400 206" fill="none" stroke="#FFFFFF" stroke-width="5"/>
      <path d="M0 18 C140 0 280 26 400 10" fill="none" stroke="#0677BA" stroke-width="4"/>
    </svg>
    <h1 class="brand-name">Brindle</h1>

    <p class="product-type">Natural Spring Water</p>
    <svg class="drop-icon" viewBox="0 0 28 38" aria-hidden="true">
      <path d="M14 2 C6 14 2 20 2 26 a12 12 0 0 0 24 0 C26 20 22 14 14 2 Z" fill="#FFFFFF"/>
    </svg>
    <p class="eco-figure">100%</p>
    <p class="eco-label">ECO-RESPONSIBLE</p>

    <p class="source-line">Sourced from<br>the Mountains</p>
    <div class="mountain-art" role="img" aria-label="Illustration of a snow-capped mountain range in blues and white"></div>

    <p class="volume">500ml</p>
    <p class="fine-print">SUSTAINABLY SOURCED WATER<br>IN A PLANT-BASED CARTON</p>
  </section>
</div>
</body>
</html>
```